Lumira Skincare packaging designs

We are need to create packaging for our skincare brand. We need two designs. One for round jars which is for creams/capsules and the second will be for bottles/serums Some products will be larger in size so please ensure the packaging design will work and there isn't a lot white/empty space

Below are the names of some of our products.
Screw-On Top Jar (25 pads- 4 inches wide) - Velvet Swipes I Skin Brightening Pads
Pump Bottle (2 oz) - AquaLoft I Hyaluronic Acid + Vitamin Serum
Pump Bottle (6oz) - The Petal Wash I Conditioning Face Cleanser
Dropper bottle (1 oz) - Morning Mist I Hydrating Moisturizer
Cream jar (1.5 oz) - Morning Mist I Hydrating Moisturizer
Capsules Jar (25 capsules in a jar)- Plume Drop I Moisture + Hydrating Capsules
Capsules Jar (25 capsules in a jar) - Pure Pulse I Impurity Capsules

We will also need help with the packing design in terms of layout of the logo, item name, desc, and ingredients on each product.

Target Market(s)

women

Industry/Entity Type

skincare, beauty

Font styles to use
Sans Serif

Colors
E54698
E96AAD
F1A4CE
F9D9EA
FCEFF6

Requirements
Must have
• Pantone color is 2052 CP HEX #DAAFCA (218 , 175 , 202)

```html
<!DOCTYPE html>
<html lang="en">
<head>
<meta charset="utf-8">
<title>Lumira Skincare – The Petal Wash packaging labels</title>
<link href="https://fonts.googleapis.com/css2?family=Barlow+Condensed:wght@500;600&family=Barlow:wght@400;500&display=swap" rel="stylesheet">
<style>
  :root {
    --canvas: #f5f5f5;
    --band-pink: #e56f8f;
    --band-pink-deep: #d9607f;
    --box-pink: #d77b95;
    --title-pink: #d85d81;
    --label-white: #ffffff;
    --label-grey: #ececec;
    --brand-white: #ffffff;
  }
  * { box-sizing: border-box; margin: 0; padding: 0; }
  html, body { width: 1200px; height: 900px; overflow: hidden; }
  body { background: var(--canvas); position: relative; font-family: "Barlow", sans-serif; }

  .label { position: absolute; overflow: hidden; background: var(--label-white); box-shadow: 0 2px 10px rgba(0,0,0,0.06); }
  .band { position: absolute; left: 0; right: 0; top: 0; display: flex; align-items: center; justify-content: center; }
  .band-pattern { position: absolute; inset: 0; background: linear-gradient(135deg, var(--band-pink) 0%, var(--band-pink-deep) 100%); }
  .brand-name {
    position: relative; color: var(--brand-white); font-family: "Barlow", sans-serif; font-weight: 500;
    letter-spacing: 0.18em; text-transform: uppercase; text-align: center; line-height: 1.25;
  }
  .product-title {
    position: absolute; left: 0; right: 0; text-align: center; color: var(--title-pink);
    font-family: "Barlow Condensed", sans-serif; font-weight: 600; text-transform: uppercase; line-height: 1;
  }
  .title-rule { position: absolute; background: var(--title-pink); }
  .product-desc {
    position: absolute; left: 0; right: 0; text-align: center; color: var(--title-pink);
    font-family: "Barlow", sans-serif; font-weight: 400; text-transform: uppercase; white-space: nowrap;
  }
  .net-size { position: absolute; left: 0; right: 0; text-align: center; color: var(--title-pink); letter-spacing: 0.2em; }

  /* Pump bottle label */
  .bottle-label { left: 87px; top: 357px; width: 260px; height: 400px; }
  .bottle-label .band { height: 144px; }
  .bottle-label .brand-name { font-size: 17px; }
  .bottle-label .product-title { top: 574px; top: 214px; font-size: 29px; }
  .bottle-label .title-rule { left: 25px; right: 25px; top: 252px; height: 2px; }
  .bottle-label .product-desc { top: 262px; font-size: 11px; letter-spacing: 0.2em; }
  .bottle-label .net-size { top: 356px; font-size: 12px; }

  /* Cream jar wrap strip */
  .jar-label { left: 426px; top: 606px; width: 243px; height: 52px; display: flex; }
  .jar-label .band { position: relative; width: 92px; height: 100%; flex: none; }
  .jar-label .brand-name { font-size: 7.5px; letter-spacing: 0.12em; }
  .jar-label .jar-text { position: relative; flex: 1; }
  .jar-label .product-title { top: 12px; font-size: 12px; text-align: left; left: 12px; }
  .jar-label .title-rule { left: 12px; width: 88px; top: 26px; height: 1px; }
  .jar-label .product-desc { top: 31px; left: 12px; text-align: left; font-size: 5.5px; letter-spacing: 0.14em; }

  /* Jar outer box front */
  .box-front { left: 400px; top: 668px; width: 292px; height: 167px; background: var(--box-pink); }
  .box-front .band { height: 100%; }
  .box-front .band-pattern { background: var(--box-pink); }
  .box-front .brand-name { font-size: 30px; letter-spacing: 0.14em; }

  /* Tube label */
  .tube-label { left: 700px; top: 175px; width: 222px; height: 658px; }
  .tube-label .band { height: 192px; }
  .tube-label .brand-name { font-size: 21px; }
  .tube-label .product-title { top: 304px; font-size: 24px; }
  .tube-label .title-rule { left: 28px; right: 28px; top: 334px; height: 2px; }
  .tube-label .product-desc { top: 342px; font-size: 9.5px; letter-spacing: 0.16em; }
  .tube-label .net-size { top: 452px; font-size: 13px; }

  /* Dropper bottle label */
  .dropper-label { left: 950px; top: 600px; width: 150px; height: 210px; background: var(--label-grey); }
  .dropper-label .band { height: 96px; }
  .dropper-label .brand-name { font-size: 11px; }
  .dropper-label .product-title { top: 120px; font-size: 16px; }
  .dropper-label .title-rule { left: 18px; right: 18px; top: 140px; height: 1px; }
  .dropper-label .product-desc { top: 145px; font-size: 6.5px; letter-spacing: 0.12em; }
  .dropper-label .net-size { top: 180px; font-size: 9px; }
</style>
</head>
<body>

  <section class="label bottle-label" aria-label="Pump bottle label">
    <div class="band">
      <div class="band-pattern" role="img" aria-label="Pink wave line pattern"></div>
      <p class="brand-name">Lumira<br>Skincare</p>
    </div>
    <h1 class="product-title">The Petal Wash</h1>
    <div class="title-rule"></div>
    <p class="product-desc">Conditioning face cleanser</p>
    <p class="net-size">6OZ</p>
  </section>

  <section class="label jar-label" aria-label="Cream jar label strip">
    <div class="band">
      <div class="band-pattern" role="img" aria-label="Pink wave line pattern"></div>
      <p class="brand-name">Lumira<br>Skincare</p>
    </div>
    <div class="jar-text">
      <h2 class="product-title">The Petal Wash</h2>
      <div class="title-rule"></div>
      <p class="product-desc">Conditioning face cleanser</p>
    </div>
  </section>

  <section class="label box-front" aria-label="Jar box front">
    <div class="band">
      <div class="band-pattern" role="img" aria-label="Faint pink contour line pattern"></div>
      <p class="brand-name">Lumira<br>Skincare</p>
    </div>
  </section>

  <section class="label tube-label" aria-label="Tube label">
    <div class="band">
      <div class="band-pattern" role="img" aria-label="Pink wave line pattern"></div>
      <p class="brand-name">Lumira<br>Skincare</p>
    </div>
    <h2 class="product-title">The Petal Wash</h2>
    <div class="title-rule"></div>
    <p class="product-desc">Conditioning face cleanser</p>
    <p class="net-size">6OZ</p>
  </section>

  <section class="label dropper-label" aria-label="Dropper bottle label">
    <div class="band">
      <div class="band-pattern" role="img" aria-label="Pink wave line pattern"></div>
      <p class="brand-name">Lumira<br>Skincare</p>
    </div>
    <h2 class="product-title">The Petal Wash</h2>
    <div class="title-rule"></div>
    <p class="product-desc">Conditioning face cleanser</p>
    <p class="net-size">6OZ</p>
  </section>

</body>
</html>
```